Business card for medical clinic

I need an upmarket, modern medical/health business card for my clinic

Contact Information for Business Card

name, address, email, qr code

```html
<!DOCTYPE html>
<html lang="en">
<head>
<meta charset="utf-8">
<title>Meridian Care Clinic – Business Card</title>
<link href="https://fonts.googleapis.com/css2?family=Montserrat:wght@400;500;700&display=swap" rel="stylesheet">
<style>
  :root {
    --backdrop: #2b2b2b;
    --card-white: #ffffff;
    --card-dark: #1b1b1b;
    --brand-blue: #1f6fa3;
    --sky-blue: #45b2e6;
    --text-light: #f2f2f2;
  }
  * { box-sizing: border-box; margin: 0; padding: 0; }
  html, body {
    width: 1200px; height: 880px; overflow: hidden;
    background: var(--backdrop);
    font-family: "Montserrat", sans-serif;
  }
  .canvas { position: relative; width: 1200px; height: 880px; }
  .card {
    position: absolute; left: 268px; width: 665px; height: 380px;
    border-radius: 26px; overflow: hidden; background: var(--card-white);
  }
  .card--front { top: 40px; }
  .card--back { top: 460px; }

  .front-brand {
    position: absolute; inset: 0;
    display: flex; flex-direction: column; align-items: center; justify-content: center;
    color: var(--brand-blue); font-weight: 700; text-align: center;
  }
  .front-brand .brand-main { font-size: 44px; letter-spacing: 3px; }
  .front-brand .brand-sub { font-size: 20px; letter-spacing: 12px; margin-top: 6px; }

  .back-panel { position: absolute; inset: 0; }

  .back-brand {
    position: absolute; left: 390px; top: 110px; width: 250px;
    color: var(--brand-blue); font-weight: 700; text-align: center;
  }
  .back-brand .brand-main { font-size: 24px; letter-spacing: 2px; }
  .back-brand .brand-sub { font-size: 12px; letter-spacing: 7px; margin-top: 4px; }

  .contact {
    position: absolute; left: 0; top: 120px; width: 300px; color: var(--text-light);
  }
  .contact__accent {
    position: absolute; left: 30px; top: 6px; width: 8px; height: 56px; background: var(--sky-blue);
  }
  .contact__name {
    margin-left: 52px; font-size: 24px; font-weight: 700; color: var(--sky-blue); letter-spacing: 0.5px;
  }
  .contact__role { margin-left: 52px; font-size: 15px; margin-top: 2px; }
  .contact__address { margin-left: 70px; margin-top: 22px; font-size: 15px; line-height: 1.45; }
  .contact__list { list-style: none; margin-left: 70px; margin-top: 22px; font-size: 15px; }
  .contact__list li { display: flex; align-items: center; gap: 10px; margin-bottom: 6px; }
  .contact__list svg { width: 16px; height: 16px; fill: var(--sky-blue); flex: none; }
</style>
</head>
<body>
<main class="canvas">
  <section class="card card--front">
    <div class="front-brand">
      <span class="brand-main">MERIDIAN CARE</span>
      <span class="brand-sub">CLINIC</span>
    </div>
  </section>

  <section class="card card--back">
    <svg class="back-panel" viewBox="0 0 665 380" preserveAspectRatio="none" aria-hidden="true">
      <rect width="665" height="380" fill="var(--card-dark)"/>
      <path d="M250 0 C 320 30 300 260 420 340 C 460 365 500 375 540 380 L665 380 L665 0 Z" fill="var(--card-white)"/>
    </svg>

    <div class="back-brand">
      <div class="brand-main">MERIDIAN CARE</div>
      <div class="brand-sub">CLINIC</div>
    </div>

    <div class="contact">
      <span class="contact__accent"></span>
      <h1 class="contact__name">DANIEL HART</h1>
      <p class="contact__role">Managing Director</p>
      <p class="contact__address">Your address, City<br>State, Zip 1234</p>
      <ul class="contact__list">
        <li>
          <svg viewBox="0 0 16 16"><path d="M3 1 L6 1 L7 5 L5 6.5 C6 9 7 10 9.5 11 L11 9 L15 10 L15 13 C15 14 14 15 13 15 C6.5 15 1 9.5 1 3 C1 2 2 1 3 1 Z"/></svg>
          <span>123 456 789</span>
        </li>
        <li>
          <svg viewBox="0 0 16 16"><path d="M1 3 H15 V13 H1 Z M2 4 L8 9 L14 4 Z" fill-rule="evenodd"/></svg>
          <span>info@youremail.com</span>
        </li>
        <li>
          <svg viewBox="0 0 16 16"><circle cx="8" cy="8" r="7"/><path d="M1 8 H15 M8 1 C5 4 5 12 8 15 C11 12 11 4 8 1" stroke="var(--card-dark)" stroke-width="1" fill="none"/></svg>
          <span>www.yourwebsite.com</span>
        </li>
      </ul>
    </div>
  </section>
</main>
</body>
</html>
```